Birchline Septic Solutions

Would like to see some single sided ones but would also like to see some double sided with one sided only being the logo. Owners name is Colin Vandro. Phone number is 555-214-0387
Services are pumping, inspections, installs, and repairs

Contact Information for Business Card

555-241-0387 Colin Vandro Alderton, OH

```html
<!DOCTYPE html>
<html lang="en">
<head>
<meta charset="utf-8">
<title>Birchline Septic Solutions — Business Cards</title>
<link rel="stylesheet" href="https://fonts.googleapis.com/css2?family=Marcellus&display=swap">
<style>
  :root {
    --backdrop: #d9d4cc;
    --card-black: #070809;
    --ink-white: #f1f1f1;
    --ink-soft: #cfcfcf;
    --accent-teal: #20a9a2;
    --forest-grey: #3b3d3f;
    --rule: rgba(255,255,255,0.16);
  }
  * { box-sizing: border-box; margin: 0; padding: 0; }
  html, body { width: 1200px; height: 900px; overflow: hidden; }
  body {
    background: var(--backdrop);
    font-family: "Marcellus", serif;
    display: flex;
    flex-direction: column;
    align-items: center;
    justify-content: center;
    gap: 40px;
  }
  .card {
    position: relative;
    width: 660px;
    height: 377px;
    background: var(--card-black);
    border-radius: 40px;
    overflow: hidden;
    color: var(--ink-white);
    box-shadow: 0 10px 24px rgba(0,0,0,0.25);
  }
  .forest-band {
    position: absolute;
    left: 0; bottom: 0;
    width: 100%;
    height: 150px;
  }
  .card-content {
    position: relative;
    z-index: 1;
    height: 100%;
    display: flex;
    flex-direction: column;
    align-items: center;
    padding-top: 62px;
  }
  .brand {
    display: flex;
    align-items: center;
    gap: 14px;
  }
  .brand-dot {
    width: 16px; height: 16px;
    border-radius: 50%;
    background: var(--accent-teal);
  }
  .brand-name {
    font-size: 31px;
    letter-spacing: 3px;
    text-transform: uppercase;
    color: var(--ink-white);
    text-align: center;
    line-height: 1.25;
  }
  .heading-line {
    margin-top: 34px;
    font-size: 19px;
    letter-spacing: 0.5px;
    color: var(--ink-white);
  }
  .rule {
    width: 300px;
    height: 1px;
    margin: 12px 0;
    background: linear-gradient(90deg, transparent, var(--rule), transparent);
  }
  .services {
    font-size: 19px;
    color: var(--ink-soft);
    letter-spacing: 0.3px;
  }
  .owner-name { color: var(--accent-teal); text-transform: uppercase; }
  .divider { color: var(--accent-teal); margin: 0 6px; }
  .contact-row {
    display: flex;
    align-items: center;
    font-size: 19px;
    color: var(--ink-soft);
  }
  .icon { width: 16px; height: 16px; margin-right: 7px; fill: var(--accent-teal); }
</style>
</head>
<body>

  <section class="card card-front">
    <svg class="forest-band" viewBox="0 0 660 150" preserveAspectRatio="none" role="img" aria-label="Silhouette of pine forest with a mountain peak along the lower edge">
      <defs>
        <linearGradient id="forestFadeFront" x1="0" y1="0" x2="0" y2="1">
          <stop offset="0" stop-color="#3b3d3f" stop-opacity="0"/>
          <stop offset="1" stop-color="#3b3d3f" stop-opacity="0.95"/>
        </linearGradient>
      </defs>
      <rect width="660" height="150" fill="url(#forestFadeFront)"/>
    </svg>
    <div class="card-content">
      <div class="brand">
        <span class="brand-dot"></span>
        <span class="brand-name">Birchline<br>Septic Solutions</span>
      </div>
      <p class="heading-line">OUR SERVICES</p>
      <div class="rule"></div>
      <p class="services">Pumping, Inspections, Installs, And Repairs</p>
    </div>
  </section>

  <section class="card card-back">
    <svg class="forest-band" viewBox="0 0 660 150" preserveAspectRatio="none" role="img" aria-label="Silhouette of pine forest with a mountain peak along the lower edge">
      <defs>
        <linearGradient id="forestFadeBack" x1="0" y1="0" x2="0" y2="1">
          <stop offset="0" stop-color="#3b3d3f" stop-opacity="0"/>
          <stop offset="1" stop-color="#3b3d3f" stop-opacity="0.95"/>
        </linearGradient>
      </defs>
      <rect width="660" height="150" fill="url(#forestFadeBack)"/>
    </svg>
    <div class="card-content">
      <div class="brand">
        <span class="brand-dot"></span>
        <span class="brand-name">Birchline<br>Septic Solutions</span>
      </div>
      <p class="heading-line"><span class="owner-name">Colin Vandro</span><span class="divider">|</span>Owners</p>
      <div class="rule"></div>
      <p class="contact-row">
        <svg class="icon" viewBox="0 0 24 24" aria-hidden="true"><path d="M6.6 10.8a15.1 15.1 0 0 0 6.6 6.6l2.2-2.2a1 1 0 0 1 1-.25 11.4 11.4 0 0 0 3.6.57 1 1 0 0 1 1 1V20a1 1 0 0 1-1 1A17 17 0 0 1 3 4a1 1 0 0 1 1-1h3.5a1 1 0 0 1 1 1c0 1.25.2 2.45.57 3.57a1 1 0 0 1-.25 1z"/></svg>
        555-241-0387<span class="divider" style="color:var(--ink-soft)">|</span>
        <svg class="icon" viewBox="0 0 24 24" aria-hidden="true"><path d="M12 2a7 7 0 0 0-7 7c0 5.25 7 13 7 13s7-7.75 7-13a7 7 0 0 0-7-7zm0 9.5A2.5 2.5 0 1 1 12 6.5a2.5 2.5 0 0 1 0 5z"/></svg>
        Alderton, OH
      </p>
    </div>
  </section>

</body>
</html>
```